Telecommunications/Power civil contractor needs business card design

Were a new telecommunications/power underground civil contractor that is looking for a new business card design. Our company colours are silver or grey and orange. Feel free to use the white background logo or the black background logo.

Target Market(s)

Local contractors, utility companies, private sector mining/energy companies, developers.

Industry/Entity Type

Telecommunications

Contact Information for Business Card

Each card will need the following info:
Persons name:
Title:
E-mail:
Phone number:
Shop Address:
Mailing Address:

Requirements
Must have
• Each card will need the following info:
• Persons name:
• Title:
• E-mail:
• Phone number:
• Shop Address:
• Mailing Address:

```html
<!DOCTYPE html>
<html lang="en">
<head>
<meta charset="UTF-8">
<title>Delvan Civil Works – Business Card</title>
<link href="https://fonts.googleapis.com/css2?family=Lato:wght@400;700;900&display=swap" rel="stylesheet">
<style>
  :root {
    --backdrop: #1d1d1d;
    --card: #f5f5f5;
    --band: #050505;
    --orange: #e8561c;
    --grey: #6b6b6b;
    --ink: #3c3c3c;
    --band-text: #e6e6e6;
  }
  html, body {
    margin: 0;
    padding: 0;
    width: 1200px;
    height: 873px;
    overflow: hidden;
    background: var(--backdrop);
    font-family: "Lato", Arial, sans-serif;
  }
  .card {
    position: absolute;
    left: 180px;
    top: 196px;
    width: 840px;
    height: 480px;
    border-radius: 26px;
    background: var(--card);
    overflow: hidden;
    box-shadow: 0 20px 50px rgba(0,0,0,.55);
  }
  .brand {
    position: absolute;
    left: 70px;
    top: 52px;
    display: flex;
    align-items: center;
    gap: 26px;
  }
  .brand-dot {
    width: 104px;
    height: 104px;
    border-radius: 50%;
    border: 8px solid var(--orange);
    box-sizing: border-box;
  }
  .brand-name {
    color: var(--orange);
    font-weight: 900;
    font-size: 42px;
    line-height: 1;
    letter-spacing: 1px;
    text-transform: uppercase;
  }
  .brand-name small {
    display: block;
    font-size: 23px;
    letter-spacing: 2px;
    margin-top: 6px;
  }
  .name-band {
    position: absolute;
    left: 0;
    top: 186px;
    width: 100%;
    height: 96px;
    background: var(--band);
    display: flex;
    align-items: center;
    justify-content: center;
  }
  .person-name {
    color: var(--orange);
    font-weight: 700;
    font-size: 28px;
    padding-right: 22px;
  }
  .divider {
    width: 2px;
    height: 48px;
    background: var(--orange);
  }
  .person-title {
    color: var(--band-text);
    font-size: 24px;
    padding-left: 22px;
  }
  .contacts {
    position: absolute;
    left: 90px;
    top: 318px;
    color: var(--ink);
    font-size: 22px;
    line-height: 1;
  }
  .row {
    display: flex;
    align-items: center;
    gap: 34px;
    margin-bottom: 20px;
  }
  .item {
    display: flex;
    align-items: center;
    gap: 10px;
  }
  .item svg { flex: none; }
  .tag { color: var(--orange); }
</style>
</head>
<body>
  <div class="card">
    <div class="brand">
      <div class="brand-dot"></div>
      <div class="brand-name">Delvan Civil<small>Works Inc</small></div>
    </div>

    <div class="name-band">
      <span class="person-name">Aaron Kessel</span>
      <span class="divider"></span>
      <span class="person-title">Chief Operating Officer</span>
    </div>

    <div class="contacts">
      <div class="row">
        <span class="item">
          <svg width="24" height="20" viewBox="0 0 24 20" aria-hidden="true"><path d="M2 7c0-3 4-5 10-5s10 2 10 5l-4 1-1-3H7L6 8 2 7z" fill="var(--orange)"/><path d="M5 10h14l2 8H3z" fill="var(--orange)"/></svg>
          412-555-0147
        </span>
        <span class="item">
          <svg width="24" height="18" viewBox="0 0 24 18" aria-hidden="true"><rect x="1" y="1" width="22" height="16" fill="var(--orange)"/><path d="M1 1l11 9 11-9" fill="none" stroke="#fff" stroke-width="1.6"/></svg>
          enquiries@delvancivilworks.com
        </span>
      </div>
      <div class="row">
        <span class="item">
          <svg width="18" height="24" viewBox="0 0 18 24" aria-hidden="true"><path d="M9 1a8 8 0 0 0-8 8c0 6 8 14 8 14s8-8 8-14a8 8 0 0 0-8-8z" fill="var(--orange)"/><circle cx="9" cy="9" r="3" fill="#fff"/></svg>
          48 Harlow Lane, Millbrook, PA 15020 <span class="tag">(Shop)</span>
        </span>
      </div>
      <div class="row">
        <span class="item">
          <svg width="18" height="24" viewBox="0 0 18 24" aria-hidden="true"><path d="M9 1a8 8 0 0 0-8 8c0 6 8 14 8 14s8-8 8-14a8 8 0 0 0-8-8z" fill="var(--orange)"/><circle cx="9" cy="9" r="3" fill="#fff"/></svg>
          #1920 Alder Street, Eastport, New York <span class="tag">(Mailing)</span>
        </span>
      </div>
    </div>
  </div>
</body>
</html>
```